Web Design Project - Shipping Industry

Goals and Objectives
The objective of the new website is to create a more modern look and feel. The site will also allow for a more effective means of communicating with members while providing the public with information and developments in the local, regional and international shipping industry.
Scope
The website will highlight the history of the organisation inclusive of text and photographs. It will take visitors through the years from beginning to present. Information on the history of the shipping industry will also be included.
It will feature current articles on the organisation, its members and stakeholders in the shipping industry. Member information as well as pertinent details regarding the organisation’s subsidiaries will be documented for the website.
Information as it relates to shipping statistics, case studies, laws and regulations, international treaties and trade documents, shipping terms, careers in shipping, job opportunities, training opportunities, information for shippers including port listing and trade lanes will be main features of the content for the website.
The Association’s community involvement, industry calendar events and related links relevant industry members will also be featured.
Target Market
• The General Public;
• Members of the organization;
• Shipping Industry Stakeholders (local, regional and international);
• Tertiary students conducting research.
• Potential employees
• Potential Business Partners
Best Practice Bench Marketing
The following websites are being looked at:
• Korvel Quayworks - http://www.korvelquayworks.example/ (preferred look)
• Tessaly Maritime Association - http://www.tma-freight.example/ (like image transition on main page)
• Drovna - http://www.drovna.example (professional look)
• PLW - http://www.pelworth.example (preferred color: blue in logo)
• Quillo - http://www.quillo.example/electronics/tv-video-audio/ (preferred look for links page: image + short text below + visit site link)
Expected Result
• 3 - 5 pages which must include: [1] main page [2] standard page [3] links page

```html
<!DOCTYPE html>
<html lang="en">
<head>
<meta charset="utf-8">
<title>The Harbour Carriers Association</title>
<link href="https://fonts.googleapis.com/css2?family=Questrial&family=Noto+Sans:wght@400;700&family=EB+Garamond:wght@400&display=swap" rel="stylesheet">
<style>
:root{
  --navy:#1f2f78;
  --nav-blue:#1f78b8;
  --bar-blue:#0c44a6;
  --bar-dark:#083a8c;
  --orange:#e8460e;
  --gold:#e29a00;
  --link-orange:#e07f00;
  --text:#333;
  --rule:#cfcfcf;
  --footer:#cccccc;
  --sea-top:#a9d8ef;
  --sea-bottom:#1d3f73;
}
*{margin:0;padding:0;box-sizing:border-box}
html,body{width:1008px;height:1200px;overflow:hidden;background:#fff}
body{font-family:"Noto Sans",sans-serif;color:var(--text)}
.page{position:relative;width:1008px;height:1200px;overflow:hidden}
.abs{position:absolute}

.brand-mark{left:108px;top:24px;width:62px;height:62px;border-radius:50%;background:var(--bar-blue)}
.brand-name{left:100px;top:96px;font-family:"EB Garamond",serif;font-size:21px;color:var(--bar-blue);white-space:nowrap}

.login-label{left:403px;top:23px;font-family:"Questrial",sans-serif;font-size:11px;letter-spacing:.6px;color:var(--navy)}
.field{top:18px;height:22px;border:2px solid #ddd;border-radius:12px;font-size:9.5px;color:#888;padding:3px 12px}
.field.user{left:506px;width:159px}
.field.pass{left:675px;width:159px}
.login-btn{left:847px;top:18px;width:60px;height:21px;background:var(--gold);border-radius:3px;color:#fff;font-family:"EB Garamond",serif;font-weight:400;font-size:11px;text-align:center;line-height:21px;letter-spacing:.5px}
.account-links{top:53px;font-size:9.5px;color:#333}
.account-links.reg{left:737px}
.account-links.forgot{left:818px}
.account-sep{left:800px;top:51px;width:1px;height:17px;background:#888}

.main-nav{top:153px;font-family:"Questrial",sans-serif;font-size:11px;color:var(--nav-blue);white-space:nowrap}
.main-nav.active{color:var(--orange)}

.announce{left:100px;top:193px;width:609px;height:53px;background:var(--bar-blue);color:#fff}
.announce .label{position:absolute;left:25px;top:19px;font-family:"Questrial",sans-serif;font-weight:700;font-size:11px;letter-spacing:.5px}
.announce .msg{position:absolute;left:155px;top:20px;font-size:9.5px;letter-spacing:.4px}
.search{left:709px;top:193px;width:197px;height:53px;background:var(--bar-dark)}
.search .label{position:absolute;left:0;width:100%;top:7px;text-align:center;font-family:"Questrial",sans-serif;font-size:10px;color:var(--gold)}
.search .box{position:absolute;left:17px;top:25px;width:144px;height:16px;background:#fff;border-radius:8px}
.search .go{position:absolute;left:156px;top:25px;width:28px;height:16px;background:var(--gold);border-radius:8px}

.hero{left:100px;top:255px;width:807px;height:381px;background:linear-gradient(180deg,var(--sea-top) 0%,#cfe9f6 40%,#4d82b2 55%,var(--sea-bottom) 100%);border:3px solid #a9d0ee}
.hero-frame{position:absolute;left:2px;top:2px;right:2px;bottom:2px;border:1px solid rgba(255,255,255,.8)}
.hero-strip{position:absolute;left:0;right:0;bottom:0;height:46px;background:rgba(20,30,50,.55)}
.hero-dots{position:absolute;right:26px;bottom:18px;display:flex;gap:11px}
.hero-dots span{width:6px;height:6px;border-radius:50%;background:#fff}
.hero-dots span.off{background:#444}

.panel-title{font-family:"Questrial",sans-serif;font-weight:700;font-size:13px;color:var(--navy)}
.panel-rule{height:1px;background:var(--rule)}
.panel-text{font-size:9.5px;line-height:11px;color:#333}
.btn{height:23px;background:var(--orange);color:#fff;font-size:9.5px;text-align:center;line-height:23px;border-radius:2px}

.about{left:100px;top:664px;width:267px;height:205px;border:1px solid #f4c56a;padding:2px}
.about-inner{position:relative;width:100%;height:100%;border:1px solid #f4c56a}

.divider{left:678px;top:669px;width:1px;height:213px;background:var(--rule)}
.side-title{font-family:"Questrial",sans-serif;font-size:14px;color:#333}
.side-list{list-style:none;font-size:9.5px;color:var(--link-orange);letter-spacing:.3px}
.side-list li{position:relative;padding-left:13px;height:15px}
.side-list li::before{content:"";position:absolute;left:0;top:4px;width:5px;height:5px;border:1px solid var(--link-orange);border-radius:50%}

.partners-rule{left:100px;top:912px;width:807px;height:1px;background:var(--rule)}
.partner{top:940px;height:50px;display:flex;align-items:center;gap:6px;font-family:"Questrial",sans-serif;font-size:14px;color:#1c4b8c;white-space:nowrap}
.partner .dot{width:22px;height:22px;border-radius:50%;background:#1c4b8c}

.footer{left:0;top:1027px;width:1008px;height:173px;background:var(--footer)}
.foot-nav{top:1052px;font-family:"Questrial",sans-serif;font-size:10px;color:var(--navy);white-space:nowrap}
.foot-mark{left:108px;top:1088px;width:42px;height:42px;border-radius:50%;background:var(--bar-blue)}
.foot-name{left:100px;top:1137px;font-family:"EB Garamond",serif;font-size:14px;color:var(--bar-blue)}
.copy{left:101px;top:1164px;font-family:"Questrial",sans-serif;font-size:9.5px;color:#666}
.connect{left:687px;top:1048px;font-family:"Questrial",sans-serif;font-size:14px;color:#555}
.feed{left:685px;top:1069px;width:222px;height:73px;background:#fff;padding:11px 13px}
.feed p{font-size:8.5px;line-height:10px;color:#333}
.feed .meta{margin-top:8px;font-size:8.5px;color:var(--orange)}
.feed .meta i{margin-left:8px}
.social{top:1148px;width:24px;height:24px;border-radius:50%;background:#1a64b0;border:2px solid #fff}
</style>
</head>
<body>
<div class="page">

  <div class="abs brand-mark" aria-hidden="true"></div>
  <div class="abs brand-name">The Harbour Carriers Association</div>

  <div class="abs login-label">MEMBER LOGIN:</div>
  <div class="abs field user">User ID</div>
  <div class="abs field pass">Password</div>
  <div class="abs login-btn">LOG IN</div>
  <div class="abs account-links reg">Register</div>
  <div class="abs account-sep"></div>
  <div class="abs account-links forgot">Forgot password?</div>

  <nav>
    <div class="abs main-nav active" style="left:101px">ABOUT US</div>
    <div class="abs main-nav" style="left:178px">SHIPPING SCHEDULE</div>
    <div class="abs main-nav" style="left:307px">NEWS</div>
    <div class="abs main-nav" style="left:358px">FAQ</div>
    <div class="abs main-nav" style="left:402px">CONTACT US</div>
    <div class="abs main-nav" style="left:499px">CANINE SERVICES</div>
    <div class="abs main-nav" style="left:618px">PORTLINK</div>
    <div class="abs main-nav" style="left:706px">LINKS</div>
  </nav>

  <div class="abs announce">
    <span class="label">ANNOUNCEMENTS:</span>
    <span class="msg">WELCOME TO THE PLW'S WEBSITE: WE WORK THE PORT OF PELWORTH...</span>
  </div>
  <div class="abs search">
    <span class="label">SEARCH SITE</span>
    <span class="box"></span>
    <span class="go"></span>
  </div>

  <div class="abs hero" role="img" aria-label="Photo of a harbour pier with cranes and a container ship under a clear sky">
    <div class="hero-frame"></div>
    <div class="hero-strip">
      <div class="hero-dots"><span class="off"></span><span></span><span></span><span></span><span></span><span></span></div>
    </div>
  </div>

  <div class="abs about">
    <div class="about-inner">
      <div class="abs panel-title" style="left:13px;top:13px">About The Association</div>
      <div class="abs panel-rule" style="left:13px;top:37px;width:241px"></div>
      <div class="abs panel-text" style="left:13px;top:55px;width:243px">
        Registered as a Trade Union, one of the primary functions of the Association is to regulate the daily supply and management of certain categories of labour on the Port.<br><br>
        In addition, the Association acts on behalf of its members in initiatives to advance industrial relations, training, security, information ...
      </div>
      <div class="abs btn" style="left:162px;top:165px;width:83px">Read More</div>
    </div>
  </div>

  <div class="abs panel-title" style="left:395px;top:672px">Invitation To Tender</div>
  <div class="abs panel-rule" style="left:395px;top:699px;width:241px"></div>
  <div class="abs panel-text" style="left:395px;top:715px;width:250px">
    The Pelworth Harbour Authority now invites sealed bids from eligible and qualified bidders for the design, development, supply and commissioning of a Port Community System for Pelworth utilizing the International Competitive Tender Procurement Methodology.<br><br>
    The design, development, delivery/commissioning period is estimated at two (2) years. .....
  </div>
  <div class="abs btn" style="left:545px;top:832px;width:83px">Read More</div>

  <div class="abs divider"></div>

  <div class="abs side-title" style="left:707px;top:673px">Links</div>
  <ul class="abs side-list" style="left:716px;top:697px">
    <li>Training Courses</li>
    <li>About the Port of Pelworth</li>
    <li>Open Tenders</li>
  </ul>
  <div class="abs side-title" style="left:707px;top:783px">Important Facts</div>
  <ul class="abs side-list" style="left:716px;top:807px">
    <li>Laws and Legislation</li>
    <li>International trade Docs</li>
    <li>Port Statistics</li>
    <li>Shipping Terms</li>
  </ul>

  <div class="abs partners-rule"></div>
  <div class="abs partner" style="left:126px"><span class="dot"></span>Orvane Line</div>
  <div class="abs partner" style="left:300px"><span class="dot"></span>Tidewell</div>
  <div class="abs partner" style="left:403px"><span class="dot"></span>Keelbrook Shipping</div>
  <div class="abs partner" style="left:590px"><span class="dot"></span>Marlow Freight</div>
  <div class="abs partner" style="left:746px"><span class="dot"></span>Dunmere Cargo</div>

  <footer>
    <div class="abs footer"></div>
    <div class="abs foot-nav" style="left:101px">ABOUT US</div>
    <div class="abs foot-nav" style="left:172px">HOW WE WORK</div>
    <div class="abs foot-nav" style="left:272px">OUR SERVICES</div>
    <div class="abs foot-nav" style="left:360px">WHY PORTLINK</div>
    <div class="abs foot-nav" style="left:463px">NEWS AND UPDATES</div>

    <div class="abs foot-mark" aria-hidden="true"></div>
    <div class="abs foot-name">The Harbour Carriers Association</div>
    <div class="abs copy">© Copyright 2012. All Rights Reserved.</div>

    <div class="abs connect">Connect With Us</div>
    <div class="abs feed">
      <p>Praesent tempus sagittis elementum. Prsent id quam erat, sit amet condimentum neque. Phasellus quis est nisi. Ut luctus adipiscing.</p>
      <div class="meta">Lorem Ipsum<i>2 hours ago</i></div>
    </div>
    <div class="abs social" style="left:686px" aria-label="Social network link"></div>
    <div class="abs social" style="left:715px" aria-label="Social network link"></div>
    <div class="abs social" style="left:744px" aria-label="Social network link"></div>
    <div class="abs social" style="left:774px" aria-label="Social network link"></div>
  </footer>

</div>
</body>
</html>
```